Business card for my new company (Accounting firm)

I need a business card for my new business Brightwell Advisory and Ledger SA. Our services are accounting, tax, audit and financial management. Our customers are small companies, start-ups and new companies. The final design has to show financial security, trust and growth. Please find our logo attached to the business card. Text for the business card: Brightwell Advisory and Ledger SA Tomas Varenholt Director and Founder Certified Accountant Tel. 022 418 57 34 tv@clairevalconseil.ch www.clairevalconseil.ch Rue des Vergières 27 1201 Geneva
Target Market(s)
Our customers are small companies, start-ups and new companies.
Industry/Entity Type
Finance And Accounting
Contact Information for Business Card
Claireval Conseil et Comptes SA
Tomas Varenholt
Directeur et Fondateur
Expert-comptable diplômé
Tél. 022 418 57 34
tv@clairevalconseil.ch
www.clairevalconseil.ch
Rue des Vergières 27
1201 Genève

```html
<!DOCTYPE html>
<html lang="fr">
<head>
<meta charset="utf-8">
<title>Claireval Conseil et Comptes SA – Cartes de visite</title>
<link rel="stylesheet" href="https://fonts.googleapis.com/css2?family=Montserrat:wght@400;500&family=Roboto:wght@400;700&display=swap">
<style>
  :root {
    --bg: #e4e5e6;
    --card: #f6f7f7;
    --ink: #3a3b3d;
    --muted: #4d4f52;
    --blue: #1e86c6;
    --blue-light: #2ea3db;
    --blue-deep: #16598f;
    --name-blue: #1a5c94;
    --rule-dark: #2f3133;
  }
  * { box-sizing: border-box; margin: 0; padding: 0; }
  html, body { width: 1200px; height: 726px; overflow: hidden; }
  body {
    background: var(--bg);
    font-family: "Roboto", Arial, sans-serif;
    position: relative;
  }
  .card {
    position: absolute;
    width: 540px;
    height: 309px;
    background: var(--card);
    overflow: hidden;
    box-shadow: 0 2px 6px rgba(0,0,0,.12);
  }
  .card-front { left: 36px; top: 208px; }
  .card-back  { left: 624px; top: 208px; }

  .wordmark {
    display: flex;
    align-items: center;
    gap: 12px;
  }
  .wordmark-square {
    width: 26px; height: 26px;
    background: var(--blue);
    flex: none;
  }
  .wordmark-name {
    font-family: "Montserrat", Arial, sans-serif;
    font-weight: 500;
    color: var(--ink);
    letter-spacing: .06em;
    text-transform: uppercase;
    line-height: 1.15;
  }
  .card-front .wordmark {
    position: absolute;
    left: 0; right: 0; top: 104px;
    justify-content: center;
  }
  .card-front .wordmark-name { font-size: 24px; }
  .card-front .wordmark-name small {
    display: block;
    font-size: 14px;
    font-weight: 500;
    letter-spacing: .18em;
  }
  .front-stripe {
    position: absolute;
    left: 0; right: 0; bottom: 28px;
    height: 7px;
    background: linear-gradient(90deg, var(--blue-deep), var(--blue-light));
  }

  .back-band {
    position: absolute;
    left: 0; top: 0; bottom: 0;
    width: 46px;
    background: linear-gradient(180deg, var(--blue) 0%, var(--blue-deep) 100%);
  }
  .back-rule {
    position: absolute;
    left: 46px; top: 0; bottom: 0;
    width: 7px;
    background: var(--rule-dark);
  }
  .card-back .wordmark {
    position: absolute;
    left: 110px; top: 44px;
  }
  .card-back .wordmark-name { font-size: 22px; }
  .card-back .wordmark-name small {
    display: block;
    font-size: 12.5px;
    letter-spacing: .18em;
  }
  .holder {
    position: absolute;
    left: 84px; top: 126px;
  }
  .holder-name {
    font-weight: 700;
    font-size: 21px;
    color: var(--name-blue);
    margin-bottom: 6px;
  }
  .holder-role {
    font-size: 12.5px;
    color: var(--muted);
    line-height: 1.35;
  }
  .contacts {
    position: absolute;
    left: 84px; top: 214px;
    font-size: 13px;
    color: var(--muted);
    list-style: none;
  }
  .contacts-row {
    display: flex;
    align-items: center;
    gap: 14px;
    margin-bottom: 9px;
  }
  .contact {
    display: flex;
    align-items: center;
    gap: 6px;
    white-space: nowrap;
  }
  .icon { width: 13px; height: 13px; fill: var(--name-blue); flex: none; }
</style>
</head>
<body>

<section class="card card-front" aria-label="Recto">
  <div class="wordmark">
    <span class="wordmark-square"></span>
    <span class="wordmark-name">Claireval<small>Conseil et Comptes</small></span>
  </div>
  <div class="front-stripe"></div>
</section>

<section class="card card-back" aria-label="Verso">
  <div class="back-band"></div>
  <div class="back-rule"></div>

  <div class="wordmark">
    <span class="wordmark-square"></span>
    <span class="wordmark-name">Claireval<small>Conseil et Comptes</small></span>
  </div>

  <div class="holder">
    <p class="holder-name">Tomas Varenholt</p>
    <p class="holder-role">Directeur et Fondateur<br>Expert-comptable diplômé</p>
  </div>

  <ul class="contacts">
    <li class="contacts-row">
      <span class="contact">
        <svg class="icon" viewBox="0 0 24 24" aria-hidden="true"><path d="M6.6 10.8a15.1 15.1 0 0 0 6.6 6.6l2.2-2.2a1 1 0 0 1 1-.25 11.4 11.4 0 0 0 3.6.57 1 1 0 0 1 1 1V20a1 1 0 0 1-1 1A17 17 0 0 1 3 4a1 1 0 0 1 1-1h3.5a1 1 0 0 1 1 1c0 1.25.2 2.45.57 3.6a1 1 0 0 1-.25 1z"/></svg>
        022 418 57 34
      </span>
      <span class="contact">
        <svg class="icon" viewBox="0 0 24 24" aria-hidden="true"><path d="M2 5h20v14H2z" fill="none"/><path d="M2 5h20v14H2V5zm2 2v.5l8 5 8-5V7H4zm0 2.8V17h16V9.8l-8 5-8-5z"/></svg>
        tv@clairevalconseil.ch
      </span>
      <span class="contact">
        <svg class="icon" viewBox="0 0 24 24" aria-hidden="true"><path d="M12 2a10 10 0 1 0 0 20 10 10 0 0 0 0-20zm6.9 9h-3a15 15 0 0 0-1.3-5.6A8 8 0 0 1 18.9 11zM12 4c.9 1.2 1.7 3.6 1.9 7h-3.8c.2-3.4 1-5.8 1.9-7zM9.4 5.4A15 15 0 0 0 8.1 11h-3a8 8 0 0 1 4.3-5.6zM5.1 13h3a15 15 0 0 0 1.3 5.6A8 8 0 0 1 5.1 13zM12 20c-.9-1.2-1.7-3.6-1.9-7h3.8c-.2 3.4-1 5.8-1.9 7zm2.6-1.4a15 15 0 0 0 1.3-5.6h3a8 8 0 0 1-4.3 5.6z"/></svg>
        www.clairevalconseil.ch
      </span>
    </li>
    <li class="contacts-row">
      <span class="contact">
        <svg class="icon" viewBox="0 0 24 24" aria-hidden="true"><path d="M12 2a7 7 0 0 0-7 7c0 5.2 7 13 7 13s7-7.8 7-13a7 7 0 0 0-7-7zm0 9.5A2.5 2.5 0 1 1 12 6.5a2.5 2.5 0 0 1 0 5z"/></svg>
        Rue des Vergières 27 1201 Genève
      </span>
    </li>
  </ul>
</section>

</body>
</html>
```